Ravnaas-Lilleby Group AS

We need a design for our company including background pictures on our web (wix-template), redesign of logo and reports. Our company delivers personality test and services to clients when hiring staff or related to organizatonal developement.

Target Market(s)

Unisex, Age 30-50, managers in private corporations

Industry/Entity Type

Recruitment

Logo Text

Bygger laget sterkt (english translate: buids your team strong)

Number of Pages Required

1 page

Font styles to use
Sans Serif

Colors
add136
34a6d7
0255a3

Requirements
Must have
• The ideal designer will be the one to bring my narrative come to life. And it will have to include the testresults report and redesign (!) of my logo. Following the attached brief in ppt:
• - the testresult report
• - redesign logo
• - graphic elements in a maritime narrative
• - including the boat, the radar, 7 GULLs, the compass etc
Nice to have
• A strong narrative with a lot of elements.
• I really like the green color in the attached breif ;-)

```html
<!DOCTYPE html>
<html lang="en">
<head>
<meta charset="utf-8">
<title>Ravnaas-Lilleby Group AS – Arbeidsstiler</title>
<link href="https://fonts.googleapis.com/css2?family=Roboto:wght@400;500;700&display=swap" rel="stylesheet">
<style>
:root{
  --navy:#1f2f78;
  --ink:#222;
  --muted:#555;
  --hero:#eceeec;
  --ground:#b6b6d6;
  --band:#626167;
  --band-line:#807f85;
  --green:#68ab6e;
  --red:#e9636a;
  --ring:#3e6bb8;
  --footer:#1b1b1b;
  --footer-line:#3a3a3a;
  --white:#fff;
}
*{margin:0;padding:0;box-sizing:border-box}
html,body{width:1200px;height:2651px;overflow:hidden}
body{position:relative;background:var(--white);font-family:"Roboto",Arial,sans-serif;color:var(--ink)}
.abs{position:absolute}

.hero{left:0;top:0;width:1200px;height:565px;background:linear-gradient(180deg,var(--hero) 0%,var(--hero) 82%,var(--ground) 82%,#a9a9cd 100%)}
.navbar{left:0;top:49px;width:1200px;height:82px;background:var(--white);box-shadow:0 1px 3px rgba(0,0,0,.08)}
.brand{left:94px;top:14px;color:var(--navy);font-weight:700}
.brand-name{font-size:34px;line-height:36px;letter-spacing:1px}
.brand-tag{font-size:11px;font-weight:500;margin-left:8px}
.nav-link{top:30px;font-size:16px;font-weight:500;color:var(--ink)}
.lang{left:1000px;top:32px;font-size:16px;font-weight:500;display:flex;align-items:center;gap:8px;white-space:nowrap}
.flag{width:20px;height:13px;background:#2b3f8f;border:2px solid #d33}

.features{left:0;top:565px;width:1200px;height:114px;background:var(--band)}
.feature{top:0;height:114px;color:var(--white)}
.feature h3{position:absolute;font-size:19px;font-weight:500;top:20px;white-space:nowrap}
.feature p{position:absolute;font-size:13.5px;line-height:20px;top:52px;width:250px;color:#e8e8e8}
.sep{top:20px;width:1px;height:76px;background:var(--band-line)}
.icon-dot{border-radius:50%;border:3px solid var(--white)}

.title{left:0;width:1200px;top:746px;text-align:center;font-size:38px;font-weight:700}
.compass{left:472px;top:930px;width:268px;height:268px;border-radius:50%;background:radial-gradient(circle closest-side,#e4e4e4 0 45%,#fff 46% 86%,var(--ring) 87% 93%,#fff 94%)}
.dir{font-size:36px;font-weight:700}
.legend{left:936px;font-size:18px;color:var(--muted)}
.legend b{display:inline-block;width:42px;font-weight:500;color:var(--ink)}

.meter-label{font-size:21px;font-weight:700;text-align:center;width:260px}
.scale{font-size:13px;color:var(--ink)}

.section-head{font-size:22px;font-weight:700;display:flex;align-items:center;gap:14px}

.grid{display:grid;grid-template-columns:119px 120px;grid-auto-rows:45px}
.grid span{display:flex;align-items:center;justify-content:center;color:var(--white);font-size:15px;font-weight:500;border:1px solid rgba(255,255,255,.5)}
.yes{background:var(--green)}
.no{background:var(--red)}
.mid{left:550px;width:102px;text-align:center;font-size:17px;color:var(--ink)}
.col-label{font-size:15px;font-weight:500;text-align:center}

.info dt{position:absolute;left:0;width:588px;text-align:right;font-size:15px}
.info dd{position:absolute;left:622px;width:420px;font-size:15px;line-height:24px}

.footer{left:0;top:2287px;width:1200px;height:364px;background:var(--footer);color:var(--white)}
.footer h4{position:absolute;top:70px;font-size:19px;font-weight:700;letter-spacing:.3px}
.footer .about{left:99px;top:112px;width:400px;font-size:14px;line-height:24px}
.social{top:210px;width:34px;height:34px;border-radius:50%;border:1px solid #888}
.links{left:574px;top:116px;list-style:none;font-size:12.5px;line-height:25px}
.contact{left:795px;top:116px;font-size:12.5px;line-height:21px}
.contact div{position:relative;padding-left:34px;margin-bottom:22px}
.contact svg{position:absolute;left:0;top:3px}
.rule{left:99px;top:295px;width:1002px;height:1px;background:var(--footer-line)}
.copy{left:0;top:320px;width:1200px;text-align:center;font-size:12px;color:#ccc}
</style>
</head>
<body>

<div class="abs hero" role="img" aria-label="Line illustration of five figures holding signs with head symbols on a pale lavender ground"></div>

<header class="abs navbar">
  <div class="abs brand"><div class="brand-name">RLG</div><div class="brand-tag">Rekruttering og utvikling</div></div>
  <span class="abs nav-link" style="left:392px">Take the PAT test</span>
  <span class="abs nav-link" style="left:562px">product Presentation</span>
  <span class="abs nav-link" style="left:753px">Company Presentation</span>
  <svg class="abs" style="left:957px;top:32px" width="16" height="16" viewBox="0 0 16 16"><circle cx="6.5" cy="6.5" r="5" fill="none" stroke="#222" stroke-width="2"/><line x1="10" y1="10" x2="15" y2="15" stroke="#222" stroke-width="2.4"/></svg>
  <div class="abs lang"><span class="flag"></span>English <svg width="10" height="6"><path d="M0 0h10L5 6z" fill="#222"/></svg></div>
</header>

<section class="abs features">
  <div class="abs feature" style="left:98px;width:320px">
    <span class="abs icon-dot" style="left:4px;top:22px;width:44px;height:44px"></span>
    <h3 style="left:70px">Recruitment</h3>
    <p style="left:70px">We are nationwide including through cooperation agreements.</p>
  </div>
  <span class="abs sep" style="left:420px"></span>
  <div class="abs feature" style="left:452px;width:320px">
    <span class="abs icon-dot" style="left:0;top:22px;width:44px;height:44px"></span>
    <h3 style="left:69px">Organizational development</h3>
    <p style="left:69px">We are nationwide including through cooperation agreements.</p>
  </div>
  <span class="abs sep" style="left:785px"></span>
  <div class="abs feature" style="left:818px;width:320px">
    <span class="abs icon-dot" style="left:2px;top:22px;width:40px;height:40px"></span>
    <h3 style="left:58px">Personality test</h3>
    <p style="left:58px">We are nationwide including through cooperation agreements.</p>
  </div>
</section>

<h1 class="abs title">Arbeidsstiler</h1>

<span class="abs dir" style="left:592px;top:840px">N</span>
<span class="abs dir" style="left:594px;top:1248px">S</span>
<span class="abs dir" style="left:386px;top:1044px">W</span>
<span class="abs dir" style="left:792px;top:1044px">E</span>
<div class="abs compass" role="img" aria-label="Compass rose with red north point and blue ring"></div>

<div class="abs legend" style="top:986px"><b>N</b>Navigator</div>
<div class="abs legend" style="top:1028px"><b>W</b>Worker</div>
<div class="abs legend" style="top:1070px"><b>S</b>Integrator</div>
<div class="abs legend" style="top:1113px"><b>E</b>Dicipline</div>

<div class="abs meter-label" style="left:298px;top:1308px">ENERGI</div>
<svg class="abs" style="left:336px;top:1354px" width="188" height="48" viewBox="0 0 188 48">
  <rect x="1" y="1" width="176" height="46" rx="3" fill="#fff" stroke="#555" stroke-width="2"/>
  <rect x="177" y="15" width="9" height="18" fill="#666"/>
  <g fill="var(--green)">
    <rect x="6" y="6" width="5" height="36"/><rect x="14" y="6" width="5" height="36"/><rect x="22" y="6" width="5" height="36"/><rect x="30" y="6" width="5" height="36"/><rect x="38" y="6" width="5" height="36"/><rect x="46" y="6" width="5" height="36"/><rect x="54" y="6" width="5" height="36"/><rect x="62" y="6" width="5" height="36"/><rect x="70" y="6" width="5" height="36"/><rect x="78" y="6" width="5" height="36"/><rect x="86" y="6" width="5" height="36"/>
  </g>
  <g fill="var(--red)">
    <rect x="96" y="6" width="5" height="36"/><rect x="104" y="6" width="5" height="36"/><rect x="112" y="6" width="5" height="36"/><rect x="120" y="6" width="5" height="36"/><rect x="128" y="6" width="5" height="36"/>
  </g>
</svg>
<span class="abs scale" style="left:334px;top:1414px">0</span>
<span class="abs scale" style="left:494px;top:1414px">100</span>

<div class="abs meter-label" style="left:640px;top:1308px">PROBLEMLØSNINGSEVNE</div>
<svg class="abs" style="left:679px;top:1354px" width="188" height="48" viewBox="0 0 188 48">
  <rect x="1" y="1" width="176" height="46" rx="3" fill="#fff" stroke="#555" stroke-width="2"/>
  <rect x="177" y="15" width="9" height="18" fill="#666"/>
  <g fill="var(--green)">
    <rect x="6" y="6" width="5" height="36"/><rect x="14" y="6" width="5" height="36"/><rect x="22" y="6" width="5" height="36"/><rect x="30" y="6" width="5" height="36"/><rect x="38" y="6" width="5" height="36"/><rect x="46" y="6" width="5" height="36"/><rect x="54" y="6" width="5" height="36"/><rect x="62" y="6" width="5" height="36"/><rect x="70" y="6" width="5" height="36"/><rect x="78" y="6" width="5" height="36"/><rect x="86" y="6" width="5" height="36"/><rect x="94" y="6" width="5" height="36"/>
  </g>
  <g fill="var(--red)">
    <rect x="104" y="6" width="5" height="36"/><rect x="112" y="6" width="5" height="36"/><rect x="120" y="6" width="5" height="36"/><rect x="128" y="6" width="5" height="36"/><rect x="136" y="6" width="5" height="36"/>
  </g>
</svg>
<span class="abs scale" style="left:677px;top:1414px">0</span>
<span class="abs scale" style="left:836px;top:1414px">100</span>

<div class="abs section-head" style="left:266px;top:1478px">
  <svg width="52" height="52" viewBox="0 0 52 52"><circle cx="26" cy="26" r="24" fill="none" stroke="var(--navy)" stroke-width="3"/><circle cx="26" cy="26" r="15" fill="none" stroke="var(--navy)" stroke-width="3"/><circle cx="26" cy="26" r="5" fill="var(--navy)"/><line x1="26" y1="26" x2="44" y2="10" stroke="var(--navy)" stroke-width="3"/></svg>
  LYTTE
</div>
<div class="abs section-head" style="left:692px;top:1478px">
  <svg width="50" height="50" viewBox="0 0 50 50"><path d="M4 18h10l22-12v38L14 32H4z" fill="var(--navy)"/><rect x="12" y="32" width="8" height="12" fill="var(--navy)"/></svg>
  SENDE
</div>

<div class="abs grid" style="left:270px;top:1578px">
  <span class="no">NO</span><span class="no">NO</span>
  <span class="yes">YES</span><span class="no">NO</span>
  <span class="yes">YES</span><span class="no">NO</span>
  <span class="yes">YES</span><span class="no">NO</span>
  <span class="yes">YES</span><span class="yes">YES</span>
  <span class="yes">YES</span><span class="yes">YES</span>
</div>

<div class="abs mid" style="top:1585px">------ 1 ------</div>
<div class="abs mid" style="top:1632px">------ 2 ------</div>
<div class="abs mid" style="top:1680px">------ 2 ------</div>
<div class="abs mid" style="top:1729px">------ 1 ------</div>
<div class="abs mid" style="top:1779px">------ 4 ------</div>
<div class="abs mid" style="top:1828px">------ 5 ------</div>

<div class="abs grid" style="left:693px;top:1578px">
  <span class="no">NO</span><span class="no">NO</span>
  <span class="no">NO</span><span class="no">NO</span>
  <span class="no">NO</span><span class="no">NO</span>
  <span class="yes">YES</span><span class="no">NO</span>
  <span class="yes">YES</span><span class="no">NO</span>
  <span class="yes">YES</span><span class="yes">YES</span>
</div>

<div class="abs col-label" style="left:270px;width:119px;top:1870px">Empati</div>
<div class="abs col-label" style="left:389px;width:120px;top:1870px">Profesjonell</div>
<div class="abs col-label" style="left:670px;width:166px;top:1870px">Overbevisningsevne</div>
<div class="abs col-label" style="left:811px;width:120px;top:1870px">Autoritet</div>

<dl class="abs info" style="left:0;top:0;width:1200px">
  <dt style="top:1932px">Name :</dt><dd style="top:1930px">John Doe</dd>
  <dt style="top:1980px">Company :</dt><dd style="top:1978px">Finibus Bonorum et Malo</dd>
  <dt style="top:2029px">Profile :</dt><dd style="top:2027px">At vero eos et accusamus et iusto odio dignissimos ducimus qui blanditiis praesentium voluptatum deleniti atque corrupti quos dolores</dd>
</dl>

<section class="abs features" style="top:2172px">
  <div class="abs feature" style="left:98px;width:320px">
    <svg class="abs" style="left:0;top:24px" width="48" height="44" viewBox="0 0 50 50"><path d="M4 18h10l22-12v38L14 32H4z" fill="#fff"/><rect x="12" y="32" width="8" height="12" fill="#fff"/></svg>
    <h3 style="left:70px">Send</h3>
    <p style="left:70px">We are nationwide including through cooperation agreements.</p>
  </div>
  <span class="abs sep" style="left:420px"></span>
  <div class="abs feature" style="left:452px;width:320px">
    <svg class="abs" style="left:0;top:22px" width="52" height="52" viewBox="0 0 52 52"><circle cx="26" cy="26" r="24" fill="none" stroke="#fff" stroke-width="3"/><circle cx="26" cy="26" r="15" fill="none" stroke="#fff" stroke-width="3"/><circle cx="26" cy="26" r="5" fill="#fff"/><line x1="26" y1="26" x2="44" y2="10" stroke="#fff" stroke-width="3"/></svg>
    <h3 style="left:69px">Receive</h3>
    <p style="left:69px">We are nationwide including through cooperation agreements.</p>
  </div>
  <span class="abs sep" style="left:785px"></span>
  <div class="abs feature" style="left:818px;width:320px">
    <span class="abs" style="left:0;top:26px;width:48px;height:40px;background:#fff;border-radius:0 0 14px 14px" role="img" aria-label="Ship icon"></span>
    <h3 style="left:66px">Clients business</h3>
    <p style="left:66px">We are nationwide including through cooperation agreements.</p>
  </div>
</section>

<footer class="abs footer">
  <h4 style="left:99px">RAVNAAS-LILLEBY GROUP AS</h4>
  <p class="abs about">Ravnaas-Lilleby Group as (RLG) is an active counselor nationally and internationally in the field of recruitment and organizational development / change.</p>
  <span class="abs social" style="left:99px"></span>
  <span class="abs social" style="left:140px"></span>
  <span class="abs social" style="left:180px"></span>

  <h4 style="left:574px">QUICK LINKS</h4>
  <ul class="abs links">
    <li>Help</li><li>FAQ</li><li>Support</li><li>Sitemap</li><li>Terms Of Use</li><li>Privacy Statement</li>
  </ul>

  <h4 style="left:795px">CONTACT US</h4>
  <div class="abs contact">
    <div><svg width="12" height="16" viewBox="0 0 12 16"><path d="M6 0a6 6 0 0 1 6 6c0 4-6 10-6 10S0 10 0 6a6 6 0 0 1 6-6z" fill="#fff"/><circle cx="6" cy="6" r="2.2" fill="#1b1b1b"/></svg>Havnegata 7, 2nd floor,<br>0150 Oslo</div>
    <div><svg width="14" height="14" viewBox="0 0 14 14"><path d="M3 0l3 3-2 2c1 2 3 4 5 5l2-2 3 3-2 3C6 14 0 8 0 3z" fill="#fff"/></svg>21 00 00 00</div>
    <div><svg width="16" height="12" viewBox="0 0 16 12"><rect width="16" height="12" fill="#fff"/><path d="M0 0l8 6 8-6" fill="none" stroke="#1b1b1b" stroke-width="1.5"/></svg>post@ravnaas-lilleby.no</div>
  </div>

  <div class="abs rule"></div>
  <p class="abs copy">Copyrights © 2017, Ravnaas-Lilleby Group . All rights reserved.</p>
</footer>

</body>
</html>
```